Artwork for New Single, ”Keep Still”

Unique design describing Silence.
Use the pictures provided for ideas.
Looking for something out the box, different.
Make this stand out. Modern times or futuristic.
Imagination welcomed.
BRINDLE ENTERTAINMENT INC.
Artist name is Brindle
Song Title: Keep Still

Target Market(s)

Millennials, Trap music listeners, Hardcore rap fans.

Colors

Designer to choose colors to be used in the design.

Requirements
Nice to have
• Bold, serious designs. Make a statement. Masculine, professional in nature.

```html
<!DOCTYPE html>
<html lang="en">
<head>
<meta charset="utf-8">
<title>Keep Still — Brindle</title>
<link rel="stylesheet" href="https://fonts.googleapis.com/css2?family=Saira+Stencil+One&family=Reenie+Beanie&display=swap">
<style>
  :root {
    --paper-light: #d9d8d3;
    --paper-mid: #a9a8a3;
    --concrete: #76746f;
    --concrete-dark: #4a4946;
    --ink: #111111;
    --title-white: #f4f1ea;
    --stroke-red: #e0141a;
  }
  html, body {
    margin: 0;
    padding: 0;
    width: 1200px;
    height: 1200px;
    overflow: hidden;
    background: var(--concrete);
  }
  .cover {
    position: relative;
    width: 1200px;
    height: 1200px;
    overflow: hidden;
  }
  .cover-art {
    position: absolute;
    inset: 0;
    width: 1200px;
    height: 1200px;
    display: block;
  }
  .single-title {
    font-family: "Saira Stencil One", "Stardos Stencil", sans-serif;
    font-weight: 400;
    fill: var(--title-white);
  }
  .artist-name {
    font-family: "Reenie Beanie", cursive;
    fill: var(--ink);
  }
</style>
</head>
<body>
<main class="cover">
  <svg class="cover-art" viewBox="0 0 1200 1200" xmlns="http://www.w3.org/2000/svg">
    <defs>
      <linearGradient id="concrete-fill" x1="0" y1="0" x2="1" y2="1">
        <stop offset="0" stop-color="#6e6d69"/>
        <stop offset="0.5" stop-color="#55534f"/>
        <stop offset="1" stop-color="#3b3a37"/>
      </linearGradient>
      <linearGradient id="top-paper-fill" x1="0" y1="0" x2="1" y2="0">
        <stop offset="0" stop-color="#a8a7a2"/>
        <stop offset="1" stop-color="#cfcec9"/>
      </linearGradient>
      <linearGradient id="sky-fill" x1="0" y1="0" x2="1" y2="0">
        <stop offset="0" stop-color="#c9c8c2"/>
        <stop offset="0.6" stop-color="#e6e5e0"/>
        <stop offset="0.85" stop-color="#8c8b87"/>
        <stop offset="1" stop-color="#3a3a38"/>
      </linearGradient>
    </defs>

    <!-- base concrete wall -->
    <rect class="wall" width="1200" height="1200" fill="url(#concrete-fill)"/>

    <!-- torn paper, top: sky with birds -->
    <polygon class="paper-top" role="img" aria-label="Pale torn-paper sky with black birds flying"
      fill="url(#top-paper-fill)"
      points="0,0 1200,0 1200,230 1080,290 960,300 830,240 700,150 560,110 420,200 320,250 180,230 0,150"/>
    <polygon class="paper-top-edge" fill="#ecebe6"
      points="560,110 620,40 650,70 600,120 560,130 420,210 405,195"/>

    <!-- middle dark band: pole and wires silhouette -->
    <polygon class="band-dark" role="img" aria-label="Dark concrete band with a telephone pole and wires in silhouette"
      fill="var(--concrete-dark)"
      points="0,160 180,240 320,260 420,210 560,130 700,170 830,260 960,320 1200,250 1200,790 0,820"/>

    <!-- red brush X -->
    <g class="red-x" fill="var(--stroke-red)">
      <polygon opacity="0.85" points="220,640 900,290 960,420 280,790"/>
      <polygon opacity="0.8" points="300,330 470,250 920,800 740,860"/>
    </g>

    <!-- title -->
    <text class="single-title" x="600" y="650" text-anchor="middle"
      font-size="360" textLength="1100" lengthAdjust="spacingAndGlyphs">KEEP STILL</text>

    <!-- torn paper, bottom: clouds over grass -->
    <polygon class="paper-bottom" role="img" aria-label="Pale cloudy sky above a dark grass horizon with a small tree"
      fill="url(#sky-fill)"
      points="0,900 120,860 260,880 420,830 560,800 690,820 820,790 960,810 1120,760 1200,770 1200,1200 0,1200"/>
    <rect class="grass-line" x="0" y="1150" width="1200" height="50" fill="var(--ink)"/>

    <!-- artist name -->
    <text class="artist-name" x="510" y="975" text-anchor="middle" font-size="200">Brindle</text>
  </svg>
</main>
</body>
</html>
```